Redesign company trifold brochure

We are rebranding our company in September and looking for a more professional design for our brochure.

What we do - providing interdisciplinary care for those supporting ill, elderly and special needs pets at home following the human hospice model of care - is very novel and our brochure is key in explaining it and our offerings.

We serve dogs and cats. Most of the animals are quite sick, elderly. I have many personal and stock photos we can use in the brochure. Please - no pictures of puppies and/or kittens.

The hard part is fitting the info and message into a clear and concise format.

It must be appealing both to pet owners and vets (who are our primary source of patients through referrals).

It should covey WARMTH, COMPASSION, PROFESSIONALISM, and EXPERTISE.

Please look at our website www.TrellisAnimalRespite.com for more info

We have until now used maroon and copper for colors - to reflect the "sunset" of the pets life. BUT are now changing to Navy, Teal and White to reflect calm, trust and competence.

We will use the same logo recolored.

Existing brochure and new logo are attached.

PLEASE ask questions!!
Updates

We have a library of stock images you are welcome to use. All have been legally acquired and we have the right to use them. You DO NOT have to use them, just sending along in case you wish to. https://www.filecrate.example/sh/qk4vrm82zd1pyno/KLQ7Ztbn-Rrfx2mh9sWpYJ4Dc?dl=0

Our colors are NAVY, TEAL and WHITE. For your reference, the navy we use is 99/87/44/55 (CMYK) The Teal we use is 76/11/44/0 (CMYK) Thank you!

Designers -- pleaseuse pictures of older pets (no puppies or kittens). Below is a link to stock photos we own that would be appropriate for use in the brochure. https://www.filecrate.example/sh/w274m6t9pxkr5da/KLRn3GsfwlTVBXEPcq_8ZNj5u?dl=0 THANK YOU!

Designers -- I would VERY much like to include a photo of a pet in a wheel chair. I have personal photos as well as (purchased) stock photos for this purpose which can be found at http://lnk.example/TARHC-Pets-in-Wheelchairs Thank you!!

Today is the last day! Many of you have submitted beautiful designs and others are rolling in. I am so appreciative of your time and energy!! Please do not let the deadline pass without YOUR very BEST entry being submitted!! Thank you! - Miriam & All of us at Trellis Animal Respite & Home Care

Target Market(s)

Pet Owners and Veterinarians

Industry/Entity Type

Pet Care

Font styles to use
Serif

Colors
0455a3
33b8a4
ffffff

Requirements
Must have
• Our logo and information about our services. Pictures of pets. Our contact info. PLEASE NOTE: this is a 2 sided brochure. Please submit both inside and outside.
Should not have
• puppies, kittens - anything off message

```html
<!DOCTYPE html>
<html lang="en">
<head>
<meta charset="utf-8">
<title>Trellis Animal Respite &amp; Home Care — Trifold Brochure</title>
<link href="https://fonts.googleapis.com/css2?family=Montserrat:wght@600;700&family=Crimson+Pro:ital,wght@0,400;0,600;1,400;1,600&family=Great+Vibes&display=swap" rel="stylesheet">
<style>
:root{
  --navy:#0c1d45;
  --teal:#2fb5a6;
  --teal-soft:#52bab0;
  --white:#ffffff;
  --ink:#3a3a3a;
  --stage:#8e8e8e;
}
*{box-sizing:border-box;margin:0;padding:0}
html,body{width:1000px;height:1200px;overflow:hidden}
body{background:var(--stage);position:relative;font-family:"Crimson Pro",Georgia,serif;color:var(--ink)}
.side-label{position:absolute;left:72px;font-family:"Montserrat",Arial,sans-serif;font-weight:700;font-size:40px;letter-spacing:2px;color:#111;transform:rotate(-90deg);transform-origin:left top}
.side-label.outside{top:410px}
.side-label.inside{top:975px}
.sheet{position:absolute;background:var(--white);box-shadow:4px 6px 10px rgba(0,0,0,.35);overflow:hidden}
.sheet.outside{left:167px;top:23px;width:733px;height:565px}
.sheet.inside{left:167px;top:608px;width:735px;height:568px}
.abs{position:absolute}
.photo{position:absolute}
.head-bar{position:absolute;background:var(--navy);color:var(--teal);font-family:"Montserrat",Arial,sans-serif;font-weight:700;text-align:center;letter-spacing:.5px}
.beliefs{position:absolute;list-style:none}
.beliefs li{position:relative;padding-left:18px;font-size:10px;line-height:1.2;margin-bottom:20px}
.beliefs.lower li{margin-bottom:24px}
.num{position:absolute;left:0;top:0;width:13px;height:13px;border-radius:50%;background:var(--teal);color:#fff;font-size:9px;line-height:13px;text-align:center;font-family:"Montserrat",Arial,sans-serif}
.contact{position:absolute;left:244px;top:68px;width:244px;text-align:center}
.org-name{font-variant:small-caps;font-size:13px;line-height:1.25;color:#222;font-weight:600;margin-bottom:11px}
.address{font-size:11px;line-height:1.3;margin-bottom:10px}
.phone{font-size:15px;color:var(--teal);font-weight:600;margin-bottom:10px;letter-spacing:.5px}
.email{font-size:10.5px}
.brand-box{position:absolute;background:var(--navy);display:flex;align-items:center;justify-content:center;gap:8px;padding:0 10px}
.brand-dot{width:22px;height:22px;border-radius:50%;background:var(--teal);flex:none}
.brand-name{font-family:"Crimson Pro",Georgia,serif;font-size:15px;line-height:1.15;color:var(--white);font-weight:400}
.social{position:absolute;left:244px;width:244px;text-align:center;font-size:11.5px;color:#222}
.sq{display:inline-block;width:15px;height:15px;background:#3b5b98;margin:0 1px;vertical-align:middle}
ul.plain{list-style:none}
ul.plain li{position:relative;padding-left:8px;font-size:10px;line-height:1.3}
ul.plain li::before{content:"•";position:absolute;left:0}
p{font-size:10.5px;line-height:1.25}
.services-list li{font-size:9.5px}
</style>
</head>
<body>

<div class="side-label outside">OUTSIDE</div>
<div class="side-label inside">INSIDE</div>

<section class="sheet outside">
  <div class="head-bar" style="left:0;top:0;width:244px;height:54px;font-size:17px;line-height:54px">WE BELIEVE</div>
  <ol class="beliefs" style="left:24px;top:75px;width:205px">
    <li><span class="num">1</span>That animals are conscious beings, capable of thought, feeling, emotion and choice.</li>
    <li><span class="num">2</span>That each animal is an individual with his or her unique needs and wishes.</li>
    <li><span class="num">3</span>That all pets deserve to be pain-free.</li>
    <li><span class="num">4</span>That the principles of human hospice and palliative care are equally powerful when applied to animals.</li>
    <li><span class="num">5</span>That an interdisciplinary team is essential to addressing the needs of pets and their families through aging and illness.</li>
  </ol>
  <div class="photo" role="img" aria-label="Photo of a tabby cat resting in green grass" style="left:0;top:314px;width:244px;height:150px;background:linear-gradient(120deg,#6b5a3e,#8a7657 45%,#6f8f3c)"></div>
  <ol class="beliefs lower" style="left:24px;top:475px;width:205px">
    <li><span class="num">6</span>That quality of life is subjective, best evaluated by the family who knows and loves the animal.</li>
    <li><span class="num">7</span>That there isn't one answer that is right for every animal or every family.</li>
  </ol>

  <div class="head-bar" style="left:244px;top:0;width:244px;height:54px;font-size:17px;line-height:54px">CONTACT US</div>
  <div class="contact">
    <div class="org-name">Trellis Animal Respite<br>&amp; Home Care</div>
    <div class="address">480 Linden Mill Road<br>Suite 210<br>Ashford, MA 01990</div>
    <div class="phone">(555) 302-TARH</div>
    <div class="email">info@TrellisAnimalRespite.com</div>
  </div>
  <div class="abs" style="left:244px;top:314px;width:244px;height:150px;background:var(--teal-soft)"></div>
  <div class="photo" role="img" aria-label="Cut-out photo of an older dog and a cat lying together" style="left:262px;top:222px;width:180px;height:140px;border-radius:50% 45% 40% 50%;background:radial-gradient(ellipse at 40% 50%,#c9954f,#a8773d 55%,rgba(140,110,80,0) 75%)"></div>
  <div class="abs" style="left:244px;top:386px;width:244px;text-align:center">
    <div style="font-family:'Montserrat',Arial,sans-serif;font-weight:700;font-size:17px;color:var(--navy)">ON THE WEB</div>
    <div style="font-size:12.5px;color:#fff;margin-top:6px">www.TrellisAnimalRespite.com</div>
  </div>
  <div class="social" style="top:472px"><span class="sq"></span><div style="margin-top:2px">TrellisRespite</div></div>
  <div class="social" style="top:518px"><span class="sq" style="background:#2aa3d9"></span><span class="sq" style="background:#c8232c"></span><span class="sq" style="background:#1a75b3"></span><div style="margin-top:2px">TrellisAnimalRespite</div></div>

  <div class="photo" role="img" aria-label="Photo of a smiling senior golden retriever outdoors" style="left:488px;top:0;width:245px;height:314px;background:linear-gradient(160deg,#2f4a1f,#b8843e 35%,#d7a35c 55%,#6f8f3a)"></div>
  <div class="abs" style="left:488px;top:314px;width:245px;height:150px;background:rgba(64,178,165,.88)"></div>
  <div class="brand-box" style="left:508px;top:255px;width:205px;height:117px"><span class="brand-dot"></span><span class="brand-name">Trellis Animal Respite<br>&amp; Home Care</span></div>
  <div class="abs" style="left:488px;top:399px;width:245px;text-align:center;color:#fff;font-size:13px;line-height:1.25">Skilled Home Care for Ill,<br>Elderly and Special Needs Animals</div>
  <div class="photo" role="img" aria-label="Soft faded photo of grass and a pet" style="left:488px;top:464px;width:245px;height:101px;background:linear-gradient(90deg,#eef0e6,#f7f5ec 55%,#dfe6cf)"></div>
  <div class="abs" style="left:488px;top:487px;width:245px;text-align:center;font-family:'Great Vibes',cursive;font-size:21px;line-height:1.05;color:#222">Compassionate Support<br>for Families</div>
</section>

<section class="sheet inside">
  <div class="photo" role="img" aria-label="Photo of an elderly shepherd mix dog lying with a tabby cat" style="left:0;top:0;width:488px;height:314px;background:linear-gradient(100deg,#f1f2f3 0%,#e8eaec 38%,#8c6a48 55%,#4a3625 75%,#c9ccd2)"></div>
  <div class="head-bar" style="left:0;top:0;width:246px;height:68px;font-size:16px;line-height:1.4;padding-top:17px">PALLIATIVE CARE<br>&amp; HOSPICE</div>
  <div class="abs" style="left:27px;top:78px;width:200px">
    <p style="margin-bottom:10px"><i><b>Palliative Care</b></i> seeks to relieve suffering and improve quality of life at all stages of illness, injury and disease, whether curable or not.</p>
    <p><i><b>Hospice</b></i> is a special kind of Palliative Care focused on those with a life expectancy of less than one year.</p>
  </div>
  <div class="abs" style="left:0;top:314px;width:246px;height:158px;background:var(--teal-soft);color:#fff;padding:14px 0 0 27px">
    <div style="font-style:italic;font-size:12px;margin-bottom:6px">Both Palliative Care and Hospice:</div>
    <ul class="plain" style="width:200px">
      <li style="margin-bottom:11px">Focus on living fully</li>
      <li style="margin-bottom:11px">Recognize and address all suffering - physical, emotional, social and spiritual</li>
      <li style="margin-bottom:11px">Use a team approach to meet the needs of the animal and his or her family</li>
      <li>Affirm life while viewing death as a natural, normal process</li>
    </ul>
  </div>
  <div class="photo" role="img" aria-label="Photo of a veterinary professional with a senior Labrador" style="left:0;top:472px;width:246px;height:96px;background:linear-gradient(90deg,#5b8fc2,#e7dcc4 50%,#f0efeb)"></div>

  <div class="abs" style="left:246px;top:314px;width:242px;height:254px;background:var(--teal-soft)"></div>
  <div class="head-bar" style="left:263px;top:292px;width:209px;height:46px;font-size:17px;line-height:46px">OUR TEAM</div>
  <div class="abs" style="left:276px;top:350px;width:200px;color:#fff">
    <div style="font-style:italic;font-size:11px;line-height:1.2;color:var(--navy);font-weight:600;margin-bottom:8px">Lead by Miriam Caldwell, C.T. our interdisciplinary team includes:</div>
    <ul class="plain">
      <li>Certified Thanatologist</li>
      <li>Certified Veterinary Technicians</li>
      <li>Interfaith Spiritual Advisor</li>
      <li>Certified Small Animal Massage Therapist</li>
      <li>Animal Care Specialists</li>
      <li>Hospice Assistants</li>
      <li>Client Care Coordinator</li>
    </ul>
  </div>
  <div class="brand-box" style="left:263px;top:494px;width:209px;height:65px"><span class="brand-dot"></span><span class="brand-name" style="font-size:14px">Trellis Animal Respite<br>&amp; Home Care</span></div>

  <div class="abs" style="left:488px;top:0;width:247px;height:568px;background:var(--white)"></div>
  <div class="abs" style="left:488px;top:316px;width:247px;height:252px;background:var(--teal-soft)"></div>
  <div class="abs" style="left:494px;top:392px;width:233px;height:168px;background:var(--white)"></div>
  <div class="abs" style="left:505px;top:16px;width:220px">
    <div style="font-family:'Montserrat',Arial,sans-serif;font-weight:700;font-size:17px;color:var(--teal);text-align:center;margin-bottom:8px">OUR SERVICES</div>
    <p style="font-size:10px;margin-bottom:8px">At Trellis Animal Respite &amp; Home Care, our only goal is to support you in providing the very best care for your beloved companion in your own home.</p>
    <p style="font-size:10px;margin-bottom:8px;color:var(--navy);font-style:italic;font-weight:600">We are here for you 24 hours a day, every day of the year.</p>
    <p style="font-size:10px;margin-bottom:7px">We work as a team to address the needs of your entire family. We come with no agenda and no prescribed plan, but rather follow your needs and wishes as they evolve and change over time. Some of the services we offer are:</p>
    <ul class="plain services-list" style="width:210px">
      <li>Visiting and support</li>
      <li>Administration of medication &amp; fluids</li>
      <li>Overnight and respite care</li>
      <li>Check-ins, exercise and play</li>
      <li>Assistance evaluating pain, quality of life, and end of life choices</li>
      <li>Coordination of care with your vet and other care professionals</li>
      <li style="width:150px">Home cooked meals and treats</li>
      <li style="width:150px">Transportation and errand running</li>
      <li style="width:150px">Equipment and supplies</li>
      <li style="width:150px">Funerals and memorials</li>
      <li style="width:150px">Bereavement support</li>
    </ul>
  </div>
  <div class="photo" role="img" aria-label="Photo of a small black dog in a wheelchair on a pink blanket" style="left:668px;top:292px;width:60px;height:88px;background:radial-gradient(ellipse at 50% 40%,#2a2a2a,#555 45%,#e8a6c2 70%,rgba(255,255,255,0) 80%)"></div>
  <div class="abs" style="left:505px;top:398px;width:220px;font-style:italic;font-weight:600;font-size:10px;color:var(--navy)">Our skilled team members can also provide:</div>
  <div class="photo" role="img" aria-label="Photo of a grey cat with a bandaged leg" style="left:494px;top:436px;width:74px;height:124px;background:linear-gradient(180deg,#f3f3f3,#8c8c8c 45%,#c77a3a 85%)"></div>
  <ul class="plain abs" style="left:575px;top:412px;width:150px">
    <li>Massage and TTouch</li>
    <li>Cold LASER Treatments</li>
    <li>Reiki</li>
    <li>Passive Range of Motion (PROM)</li>
    <li>Rehabilitation Support</li>
    <li>Grooming</li>
    <li>Essential Oils</li>
    <li>Bach Flower Essences</li>
    <li>Aroma Therapy</li>
    <li>Music Therapy</li>
    <li>Pet Therapy</li>
  </ul>
</section>

</body>
</html>
```